Marrowby Water Taxi and Transport Business Card

I need business cards for my new water taxi and freight transport business I have started here in Kodiak Alaska. Kodiak is a remote island in the middle of the gulf of Alaska. There are seven native villages around the island and Kodiak is the #2 fishing port in the United States. We also have the largest Coast Guard Base in the U.S. My company will be providing water taxi and freight transport logistics to the villages and many hunting and fishing lodges as well as remote properties around the island.

I would like a business card that isn't status quo, something that stands out, either in feel or appearance. I do like clean minimal designs but it needs to have the necessary contact info on it.

Target Market(s)

remote lodge / property owners, residents of the many villages around Kodiak and any one wanting to enjoy the great outdoors of Kodiak Alaska

Industry/Entity Type

Business

Contact Information for Business Card

I like clean simple designs that aren't cluttered but still provide the necessary information

Colors
0255a3
3277b5
33a4d5
9bcb3c
add136
fbed22
ffc214
f78f20
f37122

Requirements
Must have
• logo and contact info
• Captain Mason Elwick
• www.marrowbyferryline.com
• mason@marrowbyferryline.com

```html
<!DOCTYPE html>
<html lang="en">
<head>
<meta charset="utf-8">
<title>Marrowby Water Taxi and Transport – Business Card</title>
<link rel="stylesheet" href="https://fonts.googleapis.com/css2?family=Exo+2:wght@600&family=Questrial&display=swap">
<style>
  :root {
    --backdrop: #3b3b3b;
    --card-white: #ffffff;
    --navy: #0255a3;
    --mid-blue: #3277b5;
    --sky-blue: #33a4d5;
    --orange: #f78f20;
    --text-gray: #5a5a5a;
    --rule-gray: #d4d4d4;
    --sea-deep: #1d4f92;
    --sea-light: #5c9bd6;
    --sky-pale: #b9d8f2;
  }
  * { box-sizing: border-box; margin: 0; padding: 0; }
  html, body { width: 1105px; height: 1200px; overflow: hidden; }
  body {
    background: var(--backdrop);
    position: relative;
    font-family: "Questrial", "Century Gothic", sans-serif;
  }
  .card {
    position: absolute;
    left: 196px;
    width: 721px;
    height: 412px;
    overflow: hidden;
  }
  .card--front { top: 146px; background: var(--card-white); }
  .card--back { top: 602px; }

  /* Front */
  .logo-art {
    position: absolute;
    left: 57px; top: 88px;
    width: 243px; height: 111px;
    border-radius: 4px;
    background: linear-gradient(180deg, var(--sky-blue) 0%, #7fc2e6 55%, #c9d3dc 100%);
  }
  .wordmark {
    position: absolute;
    left: 57px; top: 208px;
    width: 243px;
    text-align: center;
    font-family: "Exo 2", sans-serif;
    font-weight: 600;
    color: var(--navy);
  }
  .wordmark__name { display: block; font-size: 39px; letter-spacing: 1px; line-height: 46px; }
  .wordmark__tag { display: block; font-size: 19px; line-height: 24px; }
  .divider {
    position: absolute;
    left: 338px; top: 88px;
    width: 1px; height: 205px;
    background: var(--rule-gray);
  }
  .contact { position: absolute; left: 381px; top: 100px; }
  .contact__name {
    font-family: "Exo 2", sans-serif;
    font-weight: 600;
    font-size: 26px;
    color: var(--navy);
    letter-spacing: 0.5px;
    line-height: 30px;
  }
  .contact__role { font-size: 21px; color: var(--orange); line-height: 28px; }
  .contact__address {
    margin-top: 14px;
    font-size: 18px;
    line-height: 23px;
    color: var(--text-gray);
    font-style: normal;
  }
  .contact__line {
    display: flex; align-items: center; gap: 10px;
    margin-top: 6px;
    font-size: 18px;
    color: var(--text-gray);
  }
  .contact__line:first-of-type { margin-top: 12px; }
  .contact__line svg { flex: none; }
  .swoosh { position: absolute; left: 0; bottom: 0; }
  .website {
    position: absolute;
    left: 43px; top: 369px;
    font-size: 18px;
    color: var(--card-white);
    letter-spacing: 0.3px;
  }

  /* Back */
  .photo {
    position: absolute; inset: 0;
    background: linear-gradient(180deg, var(--sky-pale) 0%, var(--sea-light) 18%, var(--sea-light) 22%, var(--sea-deep) 100%);
  }
  .back-wordmark {
    position: absolute;
    left: 56px; top: 262px;
    width: 235px;
    text-align: center;
    font-family: "Exo 2", sans-serif;
    font-weight: 600;
    color: var(--card-white);
  }
  .back-wordmark .wordmark__name { font-size: 38px; line-height: 44px; }
  .back-wordmark .wordmark__tag { font-size: 18px; line-height: 22px; }
  .social {
    position: absolute;
    left: 123px; top: 355px;
    display: flex; gap: 3px;
  }
  .social__dot {
    width: 30px; height: 30px;
    border-radius: 50%;
    background: var(--card-white);
  }
</style>
</head>
<body>
  <section class="card card--front">
    <div class="logo-art" role="img" aria-label="Logo illustration: boat before blue mountains and an orange sun"></div>
    <div class="wordmark">
      <span class="wordmark__name">MARROWBY</span>
      <span class="wordmark__tag">Water Taxi &amp; Transport</span>
    </div>
    <div class="divider"></div>
    <div class="contact">
      <h1 class="contact__name">MASON ELWICK</h1>
      <p class="contact__role">Captain</p>
      <address class="contact__address">412 Harbor View Road<br>Marrowby, Alaska 99615</address>
      <p class="contact__line">
        <svg width="14" height="14" viewBox="0 0 24 24" aria-hidden="true"><path fill="var(--navy)" d="M6.6 10.8a15.1 15.1 0 0 0 6.6 6.6l2.2-2.2c.3-.3.7-.4 1-.2 1.1.4 2.3.6 3.6.6.6 0 1 .4 1 1V20c0 .6-.4 1-1 1A17 17 0 0 1 3 4c0-.6.4-1 1-1h3.5c.6 0 1 .4 1 1 0 1.3.2 2.5.6 3.6.1.3 0 .7-.2 1z"/></svg>
        907 555 0148
      </p>
      <p class="contact__line">
        <svg width="15" height="11" viewBox="0 0 24 17" aria-hidden="true"><rect width="24" height="17" rx="1.5" fill="var(--navy)"/><path d="M1.5 1.5 12 9.5l10.5-8" stroke="#fff" stroke-width="1.8" fill="none"/></svg>
        mason@marrowbyferryline.com
      </p>
    </div>
    <svg class="swoosh" width="721" height="110" viewBox="0 0 721 110" aria-hidden="true">
      <defs>
        <linearGradient id="bandBlue" x1="0" x2="1" y1="0" y2="0">
          <stop offset="0" stop-color="var(--navy)"/>
          <stop offset="0.6" stop-color="var(--mid-blue)"/>
          <stop offset="1" stop-color="var(--sky-blue)"/>
        </linearGradient>
      </defs>
      <path d="M0 30 C180 -4 420 18 721 0 L721 6 C430 26 190 8 0 40 Z" fill="var(--sky-blue)"/>
      <path d="M0 44 C200 12 430 40 721 14 L721 22 C440 50 210 24 0 52 Z" fill="var(--orange)"/>
      <path d="M0 58 C220 28 450 56 721 30 L721 110 L0 110 Z" fill="url(#bandBlue)"/>
    </svg>
    <p class="website">www.marrowbyferryline.com</p>
  </section>

  <section class="card card--back">
    <div class="photo" role="img" aria-label="Photograph: water taxi cruising across a blue bay toward snow-capped mountains"></div>
    <div class="back-wordmark">
      <span class="wordmark__name">MARROWBY</span>
      <span class="wordmark__tag">Water Taxi &amp; Transport</span>
    </div>
    <div class="social" aria-hidden="true">
      <span class="social__dot"></span>
      <span class="social__dot"></span>
      <span class="social__dot"></span>
    </div>
  </section>
</body>
</html>
```